Dental Practice Billboard Design

We are a newer dental practice in need of a simple but appealing billboard for our growing dental practice to attract new patients. The practice is owned by husband and wife dentists and is family friendly in a small town in Kentucky. We try to be very friendly and caring to our patients. Would prefer a blue background for the billboard and our tooth logo to be prominent. We are partial to the Patua One font used in the image below but please feel free to tweak it as you deem necessary. The shape of the uppercase D and lowercase g are why we like that font, so fonts with a similarly shaped “D” and “g” would work as well. Please include our phone number (555) 847-1390. Please see our website Harlowbrookdentistry.example for more info on the practice if needed. Thank you! Looking forward to seeing your creation.
Updates

The dimensions will be 12ft x 24ft (3.6576m x 7.3152m). Apologies for not including this in the original prompt. Thank you all for your submissions.

Industry/Entity Type

Dental

Font styles to use
Other font styles liked:
• Patua One

Colors
0054AA
0677BA
7BADD7
CADEEF
E8F1F8
0094D4
00A9DD
6FCCEA
C7EBF8
E9F6FB
00AB8E
00BBA5
67D7C9
C6EFE9
E9F9F6
59FF00
82FF00
B8FF75
E3FFCB
F4FFEA

Requirements
Must have
• Phone number, website, Logo, Practice name “Harlow Brook Dentistry”
Should not have
• A tagline or slogan

```html
<!DOCTYPE html>
<html lang="en">
<head>
<meta charset="utf-8">
<title>Harlow Brook Dentistry Billboard</title>
<link rel="stylesheet" href="https://fonts.googleapis.com/css2?family=Patua+One&display=swap">
<style>
  :root {
    --brand-blue: #0054AA;
    --brand-green: #14B01E;
    --paper: #FFFFFF;
    --backdrop: #E8F1F8;
  }
  * { margin: 0; padding: 0; box-sizing: border-box; }
  html, body {
    width: 1200px;
    height: 712px;
    overflow: hidden;
    background: var(--backdrop);
  }
  .billboard {
    position: relative;
    width: 1200px;
    height: 712px;
    background: var(--paper);
    font-family: "Patua One", Georgia, serif;
    overflow: hidden;
  }
  .brand-mark {
    position: absolute;
    left: 58px;
    top: 92px;
    width: 300px;
    height: 300px;
    border-radius: 50%;
    background: var(--brand-blue);
  }
  .practice-name {
    position: absolute;
    left: 410px;
    top: 40px;
    color: var(--brand-blue);
    font-weight: 400;
    line-height: 1;
  }
  .practice-name__lead {
    display: block;
    font-size: 200px;
    letter-spacing: 1px;
  }
  .practice-name__rest {
    display: block;
    font-size: 88px;
    margin-top: 4px;
    margin-left: -20px;
  }
  .web-band {
    position: absolute;
    left: 395px;
    top: 388px;
    right: 0;
    height: 64px;
    background: var(--brand-green);
    display: flex;
    align-items: center;
    padding-left: 26px;
  }
  .website {
    color: var(--paper);
    font-size: 40px;
    line-height: 1;
    white-space: nowrap;
  }
  .contact-band {
    position: absolute;
    left: 0;
    right: 0;
    top: 482px;
    bottom: 0;
    background: var(--brand-blue);
    display: flex;
    align-items: center;
    justify-content: center;
    gap: 26px;
    padding-left: 130px;
  }
  .phone-icon {
    width: 64px;
    height: 64px;
    flex: none;
  }
  .phone-number {
    color: var(--paper);
    font-size: 124px;
    line-height: 1;
    letter-spacing: 1px;
    white-space: nowrap;
  }
</style>
</head>
<body>
  <main class="billboard">
    <div class="brand-mark" aria-hidden="true"></div>

    <h1 class="practice-name">
      <span class="practice-name__lead">Harlow</span>
      <span class="practice-name__rest">Brook Dentistry</span>
    </h1>

    <div class="web-band">
      <p class="website">Harlowbrookdentistry.example</p>
    </div>

    <div class="contact-band">
      <svg class="phone-icon" viewBox="0 0 64 64" aria-hidden="true">
        <circle cx="32" cy="32" r="31" fill="#FFFFFF"/>
        <path d="M24 17c2 0 3 1 4 3l2 5c1 2 0 3-1 4l-2 2c1 4 4 7 8 9l2-2c1-1 2-2 4-1l5 2c2 1 3 2 3 4 0 3-3 6-6 6-12 0-23-11-23-23 0-3 2-6 4-9z" fill="#0054AA"/>
        <path d="M36 17a12 12 0 0 1 11 11M36 23a6 6 0 0 1 5 5" fill="none" stroke="#0054AA" stroke-width="3" stroke-linecap="round"/>
      </svg>
      <p class="phone-number">(555) 847-1390</p>
    </div>
  </main>
</body>
</html>
```